Larkspur Talent IT Recruiting firm needs a business card design for Recruiters, Sourcers, and Account

We need business cards that allow us to change all contact info, names, titles (Recruiter, Sourcer, Account Manager, Director, CEO, etc) per person since we have three offices, in three cities, Phoenix, Austin, and Las Vegas. We do recruiting and contractors for IT positions (Developers, Architects, Software Engineers, Security Engineers, Help Desk, DBAs, PMs, Scrum Masters, etc.) Our client companies are very diverse from Meridian 100 to silicone Valley type start-ups.

So, while we what hip, techie, and quirky, it still needs to be professional. Primary color we use is blue, with silver as a secondary color.

Target Market(s)

IT, Technology

Industry/Entity Type

Business

Contact Information for Business Card

Company name: Larkspur Talent, Inc.
Website: www.larkspurtalent.example
Logos for Careerloop, Blipster, and Myriada

Name, Title, Office Number, Cell Number, email

Font styles to use
Serif
Sans Serif

Colors
0455a3
d5d5d5

Requirements
Nice to have
• The grey I selected below is not necessary - but, would like silver included. I included a card design (File 3: LTI early trial example.jpg) that I had started on. It's very rough, and not quite what we're looking for, but what we did like is the logo, big, maybe a bit faded, off center, goes out of frame, etc. Still looking for other ideas - you are the pros! But, just an idea of a design element we liked.

```html
<!DOCTYPE html>
<html lang="en">
<head>
<meta charset="utf-8">
<title>Larkspur Talent business card</title>
<link rel="stylesheet" href="https://fonts.googleapis.com/css2?family=Lato:wght@400;700&display=swap">
<style>
  :root {
    --page: #e9eaec;
    --blue-light: #3fb3f2;
    --blue-mid: #1f8cf5;
    --blue-deep: #0d5bf0;
    --ink: #1c1c1c;
    --accent: #1f7ff0;
    --card-white: #ffffff;
    --card-silver: #e6e7e9;
    --on-blue: #ffffff;
  }
  * { box-sizing: border-box; margin: 0; padding: 0; }
  html, body { width: 1200px; height: 900px; overflow: hidden; }
  body { background: var(--page); position: relative; font-family: "Lato", sans-serif; }

  .card {
    position: absolute;
    width: 620px;
    height: 354px;
    border-radius: 4px;
    overflow: hidden;
    box-shadow: 0 6px 18px rgba(0,0,0,0.12);
  }

  /* Front */
  .card-front {
    left: 470px; top: 70px;
    background: linear-gradient(180deg, var(--blue-light) 0%, var(--blue-mid) 50%, var(--blue-deep) 100%);
    color: var(--on-blue);
    text-align: center;
  }
  .brand-line {
    margin-top: 100px;
    display: flex;
    justify-content: center;
    align-items: center;
    gap: 16px;
  }
  .brand-dot {
    width: 40px; height: 40px;
    border-radius: 50%;
    background: var(--on-blue);
    flex: none;
  }
  .wordmark {
    font-family: "Lato", sans-serif;
    font-weight: 400;
    font-size: 46px;
    line-height: 1;
  }
  .strapline {
    margin-top: 16px;
    font-family: "Lato", sans-serif;
    font-size: 16px;
    opacity: 0.85;
  }
  .socials {
    margin-top: 28px;
    display: flex;
    justify-content: center;
    gap: 18px;
    list-style: none;
    font-size: 12px;
    opacity: 0.85;
  }
  .socials li { display: flex; align-items: center; gap: 6px; }
  .socials .dot { width: 10px; height: 10px; border-radius: 50%; background: rgba(255,255,255,0.55); }

  /* Back */
  .card-back {
    left: 130px; top: 476px;
    background: radial-gradient(ellipse at 60% 40%, var(--card-white) 0%, var(--card-silver) 100%);
  }
  .brand-disc {
    position: absolute;
    left: 58px; top: 62px;
    width: 180px; height: 180px;
    border-radius: 50%;
    background: linear-gradient(180deg, var(--blue-light), var(--blue-deep));
    display: flex; align-items: center; justify-content: center;
    color: var(--on-blue);
    font-weight: 700;
    font-size: 22px;
    line-height: 1.2;
    text-align: center;
  }
  .person {
    position: absolute;
    left: 276px; top: 80px;
  }
  .person-name { font-size: 27px; font-weight: 700; color: var(--ink); }
  .person-title { font-size: 17px; font-weight: 400; color: var(--accent); margin-top: 2px; }
  .contacts { list-style: none; margin-top: 18px; }
  .contacts li {
    display: flex; align-items: center; gap: 10px;
    font-size: 18px; color: var(--ink); line-height: 1.3;
  }
  .contacts svg { width: 13px; height: 13px; fill: var(--accent); flex: none; }

  .wave { position: absolute; left: 0; bottom: 0; width: 620px; height: 110px; }
  .website {
    position: absolute;
    right: 70px; bottom: 22px;
    color: var(--on-blue);
    font-size: 20px; font-weight: 700;
  }
</style>
</head>
<body>
  <section class="card card-front" aria-label="Card front">
    <div class="brand-line">
      <span class="brand-dot" aria-hidden="true"></span>
      <h1 class="wordmark">Larkspur Talent</h1>
    </div>
    <p class="strapline">IT recruiting and contracting</p>
    <ul class="socials">
      <li><span class="dot"></span>Myriada</li>
      <li><span class="dot"></span>Blipster</li>
      <li><span class="dot"></span>Careerloop</li>
    </ul>
  </section>

  <section class="card card-back" aria-label="Card back">
    <div class="brand-disc">Larkspur<br>Talent</div>
    <div class="person">
      <h2 class="person-name">Jordan Avery R</h2>
      <p class="person-title">Designation</p>
      <ul class="contacts">
        <li><svg viewBox="0 0 16 16" aria-hidden="true"><path d="M1 5c0-2 3-3 7-3s7 1 7 3v1h-4V5H5v1H1z M3 8h10l1 6H2z"/></svg>555 014-2290</li>
        <li><svg viewBox="0 0 16 16" aria-hidden="true"><path d="M4 0h8a1 1 0 0 1 1 1v14a1 1 0 0 1-1 1H4a1 1 0 0 1-1-1V1a1 1 0 0 1 1-1zm1 2v10h6V2z"/></svg>555 014-2290</li>
        <li><svg viewBox="0 0 16 16" aria-hidden="true"><path d="M0 3h16v10H0z M1 4l7 5 7-5" fill-rule="evenodd"/></svg>info@larkspurtalent.example</li>
      </ul>
    </div>
    <svg class="wave" viewBox="0 0 620 110" preserveAspectRatio="none" aria-hidden="true">
      <defs>
        <linearGradient id="band" x1="0" x2="1">
          <stop offset="0" stop-color="#3fb3f2"/>
          <stop offset="1" stop-color="#1f8cf5"/>
        </linearGradient>
      </defs>
      <path d="M0 0 C120 30 260 70 380 60 C470 52 540 40 620 48 V110 H0 Z" fill="url(#band)"/>
    </svg>
    <p class="website">www.larkspurtalent.example</p>
  </section>
</body>
</html>
```